Business Card Design

Looking for business card designs for a new business. there will be two cards of the same design (both lots of information below in contact info). We would like the logo diagonally across the card with the information split above and below the logo similar to sketch. happy to look at similar alternatives
Please use same colours as in logo design

Industry/Entity Type

Business

Contact Information for Business Card

Dwight Halloran
mob - 0491 738 204
ph - 02 6148 3920
fax - 02 6148 3975
email - dwight@kestrelbeams.com.au
14 Larkmoor Road, Wendaree NSW 2391

Colin Marchetti
mob - 0438 912 557
ph - 02 6148 3920
fax - 02 6148 3975
email - colin@kestrelbeams.com.au

```html
<!DOCTYPE html>
<html lang="en">
<head>
<meta charset="utf-8">
<title>Kestrel Beams – Business Cards</title>
<link rel="stylesheet" href="https://fonts.googleapis.com/css2?family=Open+Sans:wght@400;600;700&display=swap">
<style>
  :root {
    --teal: #1f7a78;
    --ink: #141414;
    --text: #2a2a2a;
    --paper: #ffffff;
    --backdrop: #e9e6e1;
    --edge: #3a3a3a;
  }
  * { box-sizing: border-box; margin: 0; padding: 0; }
  html, body {
    width: 1145px; height: 1200px; overflow: hidden;
    background: var(--backdrop);
    font-family: "Open Sans", sans-serif;
  }
  .stage { position: relative; width: 1145px; height: 1200px; }

  .card {
    position: absolute;
    background: var(--paper);
    border: 1px solid var(--edge);
    overflow: hidden;
  }
  .card--front { left: 31px; top: 27px; width: 938px; height: 538px; }
  .card--back  { left: 174px; top: 607px; width: 943px; height: 537px; }

  .side-band {
    position: absolute; left: 0; top: 0; bottom: 0; width: 114px;
    background: var(--teal);
  }
  .side-rule {
    position: absolute; left: 117px; top: 0; bottom: 0; width: 4px;
    background: var(--ink);
  }

  .brand {
    position: absolute;
    display: flex; align-items: center; gap: 18px;
  }
  .brand__mark { width: 40px; height: 40px; background: var(--teal); flex: none; }
  .brand__name {
    font-weight: 700; color: var(--ink);
    font-size: 74px; line-height: 1; letter-spacing: -1px; white-space: nowrap;
  }
  .card--front .brand { left: 150px; top: 95px; }
  .card--back .brand { left: 0; right: 0; top: 215px; justify-content: center; }

  .contact-list {
    position: absolute; left: 134px; top: 302px;
    list-style: none; font-size: 23px; color: var(--text); line-height: 35.5px;
  }
  .contact-list li { display: flex; align-items: center; gap: 6px; white-space: nowrap; }
  .contact-list svg { width: 18px; height: 18px; fill: var(--teal); flex: none; }

  .address {
    position: absolute; left: 134px; top: 472px;
    font-size: 23px; color: var(--text); white-space: nowrap;
  }
  .person {
    position: absolute; right: 28px; top: 303px;
    font-size: 29px; font-weight: 700; color: var(--teal); white-space: nowrap;
  }

  .web {
    position: absolute; left: 0; right: 0; top: 422px; text-align: center;
    font-size: 29px; color: var(--text); letter-spacing: 3px;
  }
  .web strong { font-weight: 600; }
</style>
</head>
<body>
<main class="stage">

  <section class="card card--front" aria-label="Business card front">
    <div class="side-band"></div>
    <div class="side-rule"></div>

    <div class="brand">
      <span class="brand__mark"></span>
      <span class="brand__name">Kestrel Beams</span>
    </div>

    <ul class="contact-list">
      <li>
        <svg viewBox="0 0 20 20" aria-hidden="true"><path d="M10 1a9 9 0 1 0 0 18 9 9 0 0 0 0-18zm0 2a7 7 0 1 1 0 14 7 7 0 0 1 0-14zM7 5.5c.4-.3 1-.2 1.2.2l1 1.8c.2.4.1.8-.2 1.1l-.7.6c.5 1.2 1.3 2 2.5 2.6l.6-.7c.3-.3.7-.4 1.1-.2l1.8 1c.4.2.5.8.2 1.2l-.7.8c-.5.5-1.3.7-2 .4-2.6-1-4.6-3-5.6-5.6-.3-.7-.1-1.5.4-2z"/></svg>
        02 6148 3920
      </li>
      <li>
        <svg viewBox="0 0 20 20" aria-hidden="true"><path d="M6 1h8a1.5 1.5 0 0 1 1.5 1.5v15A1.5 1.5 0 0 1 14 19H6a1.5 1.5 0 0 1-1.5-1.5v-15A1.5 1.5 0 0 1 6 1zm.5 2.5v9h7v-9zm1 10.5v1.2h1.4V14zm2.3 0v1.2h1.4V14zm2.3 0v1.2h1.4V14zM7.5 16v1.2h1.4V16zm2.3 0v1.2h1.4V16zm2.3 0v1.2h1.4V16z"/></svg>
        0438 912 557
      </li>
      <li>
        <svg viewBox="0 0 20 20" aria-hidden="true"><path d="M5 3h9v4H5zM2 8h16a1 1 0 0 1 1 1v6a1 1 0 0 1-1 1h-2v-3H4v3H2a1 1 0 0 1-1-1V9a1 1 0 0 1 1-1zm3 6h10v3H5z"/></svg>
        02 6148 3975
      </li>
      <li>
        <svg viewBox="0 0 20 20" aria-hidden="true"><path d="M10 2l9 6v10H1V8zm0 2.3L3.4 8.6 10 13l6.6-4.4zM3 10.5V16h14v-5.5L10 15z"/></svg>
        colin@kestrelbeams.com.au
      </li>
    </ul>

    <p class="address">14 Larkmoor Road, Wendaree NSW 2391</p>
    <p class="person">Colin Marchetti</p>
  </section>

  <section class="card card--back" aria-label="Business card back">
    <div class="brand">
      <span class="brand__mark"></span>
      <span class="brand__name">Kestrel Beams</span>
    </div>
    <p class="web">www.<strong>kestrelbeams</strong>.com.au</p>
  </section>

</main>
</body>
</html>
```